Tarn Workforce Tri Fold Brochure

My company is a recruiting/staffing firm. I need a design that is going to be professional, bright, young, hip and fun. Pictures are key! We want people working in an office, packaging, food production and/or light industrial environment. Must embrace DIVERSITY. Please use the 4 primary colors from the Tarn Logo to accent the piece, but not too busy. I am including the content that I would like to be included in the trifold as well as a sample of a trifold I have used in the past in addition to a couple of logos. My website is www.TarnWorkforce-example.com for look and feel.

Target Market(s)

Logistics, Distribution and Manufacturing companies

Industry/Entity Type

Staffing

Requirements
Must have
• Clean, colorful, eye catching, great pictures and graphics. Photo's of diverse people working, in a office, or production setting.
Nice to have
• Must be professional
Should not have
• Not too busy.

```html
<!DOCTYPE html>
<html lang="en">
<head>
<meta charset="utf-8">
<title>Tarn Workforce Tri-Fold Brochure</title>
<link rel="stylesheet" href="https://fonts.googleapis.com/css2?family=Oswald:wght@500;700&family=Open+Sans:wght@400;600;700&display=swap">
<style>
  :root{
    --navy:#2b2a6e;
    --navy-deep:#222158;
    --yellow:#f2c31b;
    --red:#d8322b;
    --green:#39a547;
    --white:#ffffff;
    --ink:#3a3a4a;
    --paper:#ecebe8;
    --photo-warm:#b59a86;
    --photo-cool:#8ea0b8;
  }
  *{box-sizing:border-box;margin:0;padding:0}
  html,body{width:1200px;height:2400px;overflow:hidden}
  body{background:var(--paper);font-family:"Open Sans",Arial,sans-serif;color:var(--ink);position:relative}
  .spread{position:absolute;left:30px;width:1140px;height:880px;display:flex;box-shadow:0 8px 30px rgba(0,0,0,.18);background:var(--white)}
  .spread--outside{top:200px}
  .spread--inside{top:1320px}
  .panel{position:relative;width:380px;height:880px;overflow:hidden}
  .abs{position:absolute}
  .shapes{position:absolute;left:0;top:0}
  .photo{position:absolute}
  .photo--warm{background:linear-gradient(135deg,#d7c7b8,var(--photo-warm) 55%,#6d6470)}
  .photo--cool{background:linear-gradient(135deg,#c9d3e0,var(--photo-cool) 55%,#5b6680)}
  .photo--round{border-radius:50%;border:6px solid var(--white)}

  .wordmark{display:flex;align-items:center;gap:10px;font-family:"Open Sans",Arial,sans-serif;font-weight:700;color:var(--navy);letter-spacing:.5px}
  .wordmark__dot{width:14px;height:14px;border-radius:50%;background:var(--yellow)}

  .definition{font-size:12px;line-height:1.55}
  .definition strong{color:var(--navy);font-size:14px}
  .tag{display:inline-block;background:var(--navy);color:var(--white);font-size:11px;font-weight:700;letter-spacing:1px;padding:4px 12px;margin-bottom:8px}
  .copy{font-size:11.5px;line-height:1.55}

  .contact-pill{left:120px;top:205px;width:140px;border:1.5px solid var(--yellow);color:var(--yellow);font-size:12px;font-weight:700;letter-spacing:1.5px;text-align:center;padding:5px 0;border-radius:3px}
  .offices{left:34px;top:260px;width:320px;display:grid;grid-template-columns:1fr 1fr;gap:18px 20px;color:var(--white)}
  .office__state{font-family:"Oswald",Arial,sans-serif;font-size:15px;letter-spacing:1px;color:var(--yellow);margin-bottom:6px}
  .office__line{display:flex;align-items:flex-start;gap:6px;font-size:11px;line-height:1.35;margin-bottom:6px}
  .office__line svg{flex:none;margin-top:1px}
  .back-contact{left:70px;top:700px;width:290px;color:var(--navy);font-size:15px;line-height:1.5;text-align:right;font-weight:600}

  .cover-title{left:0;top:765px;width:380px;text-align:center;font-family:"Oswald",Arial,sans-serif;font-weight:700;font-size:40px;line-height:1.05;color:var(--navy);letter-spacing:.5px}

  .section-title{font-family:"Oswald",Arial,sans-serif;font-weight:700;font-size:26px;letter-spacing:1px}
  .what-we-do{left:30px;top:420px;width:320px;color:var(--white)}
  .what-we-do .section-title{color:var(--yellow);margin-bottom:12px}
  .what-we-do .copy{margin-bottom:10px}

  .options{left:34px;top:245px;width:316px}
  .options .section-title{color:var(--navy);text-align:center;margin-bottom:24px}
  .option{display:flex;gap:14px;margin-bottom:26px}
  .option__icon{flex:none;width:44px;height:44px;border-radius:50%;background:var(--yellow);display:flex;align-items:center;justify-content:center}
  .option__name{font-family:"Oswald",Arial,sans-serif;font-size:15px;color:var(--navy);letter-spacing:1px;margin-bottom:4px}

  .onsite{left:30px;top:40px;width:320px;color:var(--white)}
  .onsite .section-title{color:var(--yellow);border-bottom:2px solid var(--yellow);padding-bottom:4px;margin-bottom:10px}
  .sector{margin-top:16px}
  .sector__label{display:inline-block;color:var(--white);font-size:11.5px;font-weight:700;letter-spacing:1px;padding:4px 14px;border-radius:0 12px 12px 0;margin-bottom:8px}
  .sector__label--red{background:var(--red)}
  .sector__label--green{background:var(--green)}
  .sector__label--yellow{background:var(--yellow);color:var(--navy)}
  .sector__list{list-style:none;display:grid;grid-template-columns:1fr 1fr;gap:3px 12px;font-size:11.5px}
  .sector__list li::before{content:"";display:inline-block;width:6px;height:6px;border-radius:50%;background:var(--yellow);margin-right:7px;vertical-align:middle}
</style>
</head>
<body>

<!-- OUTSIDE SPREAD -->
<section class="spread spread--outside">

  <!-- inside flap -->
  <article class="panel panel--flap">
    <div class="photo photo--warm" style="left:0;top:630px;width:380px;height:250px" role="img" aria-label="Photo of a diverse team collaborating around a table with laptops and papers"></div>
    <svg class="shapes" width="380" height="880" viewBox="0 0 380 880">
      <path d="M0 0H380V650Q190 610 0 700Z" fill="var(--white)"/>
      <path d="M0 700Q190 610 380 650" fill="none" stroke="var(--navy)" stroke-width="16"/>
    </svg>
    <div class="wordmark abs" style="left:30px;top:34px;font-size:22px"><span>Tarn Workforce</span><span class="wordmark__dot"></span></div>
    <p class="definition abs" style="left:30px;top:90px;width:320px">DEFINITION OF TARN – noun<br><strong>a small, still mountain lake; calm, clear and steady.</strong><br>"We help every hire settle in like water finding its level."</p>
    <div class="abs" style="left:30px;top:200px;width:320px">
      <span class="tag">ABOUT US</span>
      <p class="copy">Tarn Workforce is a full service staffing partner built on trust. We connect people with the right roles and give clients a steady team they can rely on every single day.</p>
    </div>
    <div class="abs" style="left:30px;top:330px;width:320px">
      <span class="tag">OUR MISSION</span>
      <p class="copy">We are committed to helping businesses grow by placing skilled, motivated people in every shift. Our team listens first, then builds a plan that fits your goals, your culture and your schedule.</p>
      <p class="copy" style="margin-top:8px">Tarn Workforce is a values driven company that treats every candidate with respect and every client as a long term partner.</p>
    </div>
  </article>

  <!-- back panel -->
  <article class="panel panel--back" style="background:var(--navy)">
    <svg class="shapes" width="380" height="880" viewBox="0 0 380 880">
      <path d="M0 660Q200 620 380 560V880H0Z" fill="var(--yellow)"/>
      <path d="M0 650Q200 610 380 548" fill="none" stroke="var(--navy-deep)" stroke-width="6"/>
    </svg>
    <div class="photo photo--cool photo--round" style="left:115px;top:40px;width:150px;height:150px" role="img" aria-label="Photo of a smiling office worker at a computer"></div>
    <div class="contact-pill abs">CONTACT US</div>
    <div class="offices abs">
      <div class="office">
        <div class="office__state">GEORGIA</div>
        <div class="office__line"><svg width="10" height="13" viewBox="0 0 10 13"><path d="M5 0a5 5 0 0 0-5 5c0 4 5 8 5 8s5-4 5-8a5 5 0 0 0-5-5zm0 7a2 2 0 1 1 0-4 2 2 0 0 1 0 4z" fill="var(--yellow)"/></svg><span>Millbrook<br>555-0148</span></div>
        <div class="office__line"><svg width="10" height="13" viewBox="0 0 10 13"><path d="M5 0a5 5 0 0 0-5 5c0 4 5 8 5 8s5-4 5-8a5 5 0 0 0-5-5zm0 7a2 2 0 1 1 0-4 2 2 0 0 1 0 4z" fill="var(--yellow)"/></svg><span>Cedar Falls<br>555-0121</span></div>
        <div class="office__line"><svg width="10" height="13" viewBox="0 0 10 13"><path d="M5 0a5 5 0 0 0-5 5c0 4 5 8 5 8s5-4 5-8a5 5 0 0 0-5-5zm0 7a2 2 0 1 1 0-4 2 2 0 0 1 0 4z" fill="var(--yellow)"/></svg><span>Oakridge<br>555-0133</span></div>
        <div class="office__line"><svg width="10" height="13" viewBox="0 0 10 13"><path d="M5 0a5 5 0 0 0-5 5c0 4 5 8 5 8s5-4 5-8a5 5 0 0 0-5-5zm0 7a2 2 0 1 1 0-4 2 2 0 0 1 0 4z" fill="var(--yellow)"/></svg><span>Pine Hollow<br>555-0172</span></div>
      </div>
      <div class="office">
        <div class="office__state">INDIANA</div>
        <div class="office__line"><svg width="10" height="13" viewBox="0 0 10 13"><path d="M5 0a5 5 0 0 0-5 5c0 4 5 8 5 8s5-4 5-8a5 5 0 0 0-5-5zm0 7a2 2 0 1 1 0-4 2 2 0 0 1 0 4z" fill="var(--yellow)"/></svg><span>Riverside<br>555-0185</span></div>
        <div class="office__state" style="margin-top:14px">PENNSYLVANIA</div>
        <div class="office__line"><svg width="10" height="13" viewBox="0 0 10 13"><path d="M5 0a5 5 0 0 0-5 5c0 4 5 8 5 8s5-4 5-8a5 5 0 0 0-5-5zm0 7a2 2 0 1 1 0-4 2 2 0 0 1 0 4z" fill="var(--yellow)"/></svg><span>Hillcrest<br>555-0164</span></div>
        <div class="office__state" style="margin-top:14px">TEXAS</div>
        <div class="office__line"><svg width="10" height="13" viewBox="0 0 10 13"><path d="M5 0a5 5 0 0 0-5 5c0 4 5 8 5 8s5-4 5-8a5 5 0 0 0-5-5zm0 7a2 2 0 1 1 0-4 2 2 0 0 1 0 4z" fill="var(--yellow)"/></svg><span>Lone Mesa<br>555-0190</span></div>
      </div>
    </div>
    <div class="back-contact abs">
      555-0148 OFFICE<br>
      www.TarnWorkforce-example.com<br>
      418 Alder Row,<br>
      Suite 12, Millbrook, GA 30000
    </div>
  </article>

  <!-- front cover -->
  <article class="panel panel--cover">
    <div class="photo photo--warm" style="left:0;top:150px;width:380px;height:600px" role="img" aria-label="Photo of a confident professional woman in glasses with colleagues seated behind her in a bright office"></div>
    <svg class="shapes" width="380" height="880" viewBox="0 0 380 880">
      <path d="M0 0H380V170Q200 230 0 190Z" fill="var(--white)"/>
      <path d="M0 192Q200 232 380 172" fill="none" stroke="var(--navy)" stroke-width="10"/>
      <path d="M0 206Q200 246 380 186" fill="none" stroke="var(--yellow)" stroke-width="6"/>
      <path d="M0 740Q190 700 380 660V880H0Z" fill="var(--navy)"/>
      <path d="M0 756Q190 716 380 680V880H0Z" fill="var(--yellow)"/>
    </svg>
    <div class="wordmark abs" style="left:0;top:70px;width:380px;justify-content:center;font-size:34px"><span>Tarn Workforce</span><span class="wordmark__dot"></span></div>
    <h1 class="cover-title abs">ATTAINING CLIENT<br>OBJECTIVES</h1>
  </article>
</section>

<!-- INSIDE SPREAD -->
<section class="spread spread--inside">

  <!-- what we do -->
  <article class="panel panel--what" style="background:var(--navy)">
    <div class="photo photo--warm" style="left:0;top:0;width:380px;height:380px" role="img" aria-label="Photo of co-workers reviewing a tablet together in a warehouse break area"></div>
    <svg class="shapes" width="380" height="880" viewBox="0 0 380 880">
      <path d="M0 340Q190 410 380 350V380Q190 440 0 370Z" fill="var(--yellow)"/>
      <path d="M0 370Q190 440 380 380V880H0Z" fill="var(--navy)"/>
    </svg>
    <div class="what-we-do abs">
      <h2 class="section-title">WHAT WE DO</h2>
      <p class="copy">At Tarn Workforce we do things a little differently. We take the time to learn your operation, your people and your goals before we recommend a single candidate. That focus keeps turnover low and productivity high.</p>
      <p class="copy">We believe in providing our partners with more than a resume. Every candidate is screened, interviewed and prepared so they arrive ready to work on day one.</p>
      <p class="copy">With decades of combined experience in logistics, distribution and manufacturing, our team understands the pace of your floor and the skills your roles demand.</p>
      <p class="copy">We look forward to learning about your needs and showing how Tarn Workforce can bring steady, reliable talent to your business.</p>
    </div>
  </article>

  <!-- staffing options -->
  <article class="panel panel--options">
    <svg class="shapes" width="380" height="880" viewBox="0 0 380 880">
      <path d="M0 0H380V90Q190 140 0 100Z" fill="var(--navy)"/>
      <path d="M0 820Q190 790 380 840V880H0Z" fill="var(--navy)"/>
      <circle cx="190" cy="135" r="92" fill="var(--yellow)"/>
    </svg>
    <div class="photo photo--cool photo--round" style="left:103px;top:48px;width:174px;height:174px" role="img" aria-label="Photo of production workers in safety vests and hard hats on a factory floor"></div>
    <div class="options abs">
      <h2 class="section-title">STAFFING OPTIONS</h2>
      <div class="option">
        <div class="option__icon"><svg width="24" height="24" viewBox="0 0 24 24"><circle cx="12" cy="12" r="9" fill="none" stroke="var(--navy)" stroke-width="2.2"/><path d="M12 7v5l3.5 2.5" fill="none" stroke="var(--navy)" stroke-width="2.2" stroke-linecap="round"/></svg></div>
        <div>
          <div class="option__name">TEMPORARY</div>
          <p class="copy">An ideal solution for seasonal peaks, special projects and coverage gaps. We supply trained workers quickly so your lines keep moving without added payroll burden.</p>
        </div>
      </div>
      <div class="option">
        <div class="option__icon"><svg width="24" height="24" viewBox="0 0 24 24"><path d="M4 12h14M13 6l6 6-6 6" fill="none" stroke="var(--navy)" stroke-width="2.4" stroke-linecap="round" stroke-linejoin="round"/></svg></div>
        <div>
          <div class="option__name">TEMP TO HIRE</div>
          <p class="copy">Try before you commit. Evaluate a candidate on the job for an agreed period, then bring them on full time once you are confident they are the right fit.</p>
        </div>
      </div>
      <div class="option">
        <div class="option__icon"><svg width="24" height="24" viewBox="0 0 24 24"><path d="M5 12.5l4.5 4.5L19 7.5" fill="none" stroke="var(--navy)" stroke-width="2.6" stroke-linecap="round" stroke-linejoin="round"/></svg></div>
        <div>
          <div class="option__name">DIRECT HIRE</div>
          <p class="copy">When a role needs a long term owner, we recruit, screen and present qualified finalists so you can hire with confidence and save valuable time.</p>
        </div>
      </div>
    </div>
  </article>

  <!-- onsite management -->
  <article class="panel panel--onsite" style="background:var(--navy)">
    <div class="photo photo--cool" style="left:0;top:650px;width:380px;height:230px" role="img" aria-label="Photo of warehouse staff checking inventory on a tablet beside packed boxes"></div>
    <svg class="shapes" width="380" height="880" viewBox="0 0 380 880">
      <path d="M0 0H380V650Q190 700 0 680Z" fill="var(--navy)"/>
      <path d="M0 680Q190 700 380 650" fill="none" stroke="var(--yellow)" stroke-width="10"/>
    </svg>
    <div class="onsite abs">
      <h2 class="section-title">ONSITE MANAGEMENT</h2>
      <p class="copy">For larger teams we place a dedicated Tarn Workforce coordinator at your facility to handle scheduling, attendance, training and daily reporting, so your supervisors can focus on production.</p>
      <div class="sector">
        <span class="sector__label sector__label--red">LIGHT INDUSTRIAL</span>
        <ul class="sector__list"><li>Manufacturing</li><li>Production</li><li>Logistics</li><li>Warehouse</li><li>Packaging</li><li>Hospitality</li><li>Assembly</li></ul>
      </div>
      <div class="sector">
        <span class="sector__label sector__label--green">SKILLED TRADES</span>
        <ul class="sector__list"><li>Electrical</li><li>CNC Operators</li><li>Maintenance</li><li>Forklift Operation</li><li>Welding</li><li>Plumbing</li><li>Painting</li></ul>
      </div>
      <div class="sector">
        <span class="sector__label sector__label--yellow">OFFICE / CLERICAL</span>
        <ul class="sector__list"><li>Accounting</li><li>Data Entry</li><li>Administrative</li><li>Management</li><li>Call Center</li><li>Legal</li><li>Customer Service</li><li>Sales</li></ul>
      </div>
    </div>
  </article>
</section>

</body>
</html>
```